Australian Trucking Company Requires Professional Looking Stationary

We require a professional looking stationary design that incorporates our newly designed logo.

Our business, called "Brell Haulage Contracting", provides contracting work, transport and logistics to business in Western Australia particularly with links to the mining sector.

We are a small business looking to expand and our new logo and our new stationary will help develop our brand image in our market place.

Target Market(s)

Businesses and Corporation with links to the Mining Sector

Industry/Entity Type

Small Business

Requirements
Must have
• The letterhead must have the following details:
The new logo

Text saying: "Brell Holdings Pty Ltd (ACN 582 316 907) ATF The Brell Discretionary Trust T/AS"
"ABN 71 834 209 553"
Address "P.O Box 817 Wattlegrove WA, 6958"
Phone: 08 9352 7140
Email: brellhaul@mailbox-example.com.au

The text on the letterhead should be editable as the details are likely to change in the near future. Provision should be made for a website address all though one isn't available at the moment.

The styling, layout and font text is entirely up to the designer.

```html
<!DOCTYPE html>
<html lang="en">
<head>
<meta charset="utf-8">
<title>Brell Haulage Contracting – Business Card</title>
<link rel="stylesheet" href="https://fonts.googleapis.com/css2?family=Arimo:wght@400;700&display=swap">
<style>
  :root {
    --page-bg: #e9e6e2;
    --card-white: #ffffff;
    --red-dark: #760709;
    --red-bright: #c9141c;
    --brand-red: #c0141b;
    --text-light: #ffffff;
    --truck-grey: #6a6a6a;
    --truck-faint: #e4e4e4;
    --truck-pink: rgba(232, 170, 170, 0.72);
    --swoosh: #1c1c1c;
  }
  * { margin: 0; padding: 0; box-sizing: border-box; }
  html, body {
    width: 1200px; height: 1200px; overflow: hidden;
    background: var(--page-bg);
    font-family: "Arimo", Arial, sans-serif;
  }
  .card {
    position: absolute;
    width: 840px; height: 480px;
    overflow: hidden;
    box-shadow: 0 4px 14px rgba(0,0,0,0.18);
  }

  /* Front */
  .card-front { left: 84px; top: 78px; background: var(--card-white); }
  .front-panel { position: absolute; inset: 0; }
  .brand-icon {
    position: absolute; left: 32px; top: 22px; width: 152px; height: 124px;
    border-radius: 10px;
    background: linear-gradient(180deg, #8a8a8a, var(--truck-grey));
  }
  .brand-name {
    position: absolute; left: 214px; top: 36px;
    color: var(--brand-red);
    font-weight: 700; font-size: 40px; line-height: 44px;
    text-transform: uppercase;
  }
  .bg-truck {
    position: absolute; left: 152px; top: 242px; width: 288px; height: 238px;
    border-radius: 14px 14px 0 0;
    background: linear-gradient(180deg, #ececec, var(--truck-faint));
  }
  .person {
    position: absolute; right: 30px; top: 180px; text-align: right;
    color: var(--text-light);
  }
  .person-name { font-weight: 700; font-size: 32px; line-height: 38px; }
  .person-title { font-size: 24px; letter-spacing: 2px; line-height: 34px; }
  .contact-list {
    position: absolute; right: 26px; top: 314px; list-style: none;
    color: var(--text-light); font-size: 19px; text-align: right;
  }
  .contact-list li {
    display: flex; justify-content: flex-end; align-items: center;
    height: 33px; gap: 14px;
  }
  .contact-list li.no-icon { padding-right: 30px; height: 26px; margin-top: -6px; }
  .contact-list svg { width: 16px; height: 16px; flex: none; }

  /* Back */
  .card-back {
    left: 284px; top: 650px;
    background: linear-gradient(90deg, var(--red-dark) 0%, #a80c10 50%, var(--red-bright) 100%);
  }
  .back-truck {
    position: absolute; left: 0; top: 2px; width: 428px; height: 476px;
    border-radius: 30px 40px 0 0;
    background: linear-gradient(180deg, var(--truck-pink), rgba(232,170,170,0.6));
  }
  .web-address {
    position: absolute; right: 38px; top: 116px;
    color: var(--text-light); font-size: 28px; letter-spacing: 2px;
  }
  .web-address strong { font-weight: 700; letter-spacing: 3px; }
  .legal {
    position: absolute; left: 427px; top: 374px;
    color: var(--text-light); font-size: 21px; line-height: 30px;
  }
</style>
</head>
<body>

<section class="card card-front">
  <svg class="front-panel" width="840" height="480" viewBox="0 0 840 480">
    <defs>
      <linearGradient id="frontRed" x1="0" x2="1" y1="0" y2="0">
        <stop offset="0" stop-color="#760709"/>
        <stop offset="1" stop-color="#c9141c"/>
      </linearGradient>
    </defs>
    <path d="M840,0 C650,70 470,240 444,480 L840,480 Z" fill="url(#frontRed)"/>
    <path d="M832,2 C632,80 458,250 434,480" fill="none" stroke="var(--swoosh)" stroke-width="5"/>
    <path d="M836,1 C640,76 464,246 439,480" fill="none" stroke="#d8d8d8" stroke-width="2"/>
  </svg>

  <div class="brand-icon" role="img" aria-label="Grey truck icon beside the company name"></div>
  <div class="brand-name">Brell<br>Haulage<br>Contracting</div>

  <div class="bg-truck" role="img" aria-label="Faint grey illustration of a prime mover truck"></div>

  <div class="person">
    <div class="person-name">Your Name</div>
    <div class="person-title">Title</div>
  </div>

  <ul class="contact-list">
    <li>08 9352 7140
      <svg viewBox="0 0 16 16"><circle cx="8" cy="8" r="7" fill="none" stroke="#fff" stroke-width="1.4"/><path d="M5.5 4.5 L7 4.2 7.6 6.4 6.6 7.2 Q7.4 9 8.8 9.6 L9.6 8.6 11.6 9.2 11.4 10.8 Q7 11.2 5.5 4.5Z" fill="#fff"/></svg>
    </li>
    <li>brellhaul@mailbox-example.com.au
      <svg viewBox="0 0 16 16"><rect x="1.5" y="3.5" width="13" height="9" fill="#fff"/><path d="M1.5 3.5 L8 9 14.5 3.5" fill="none" stroke="#a80c10" stroke-width="1.2"/></svg>
    </li>
    <li>www.brellhaul-example.com
      <svg viewBox="0 0 16 16" fill="none" stroke="#fff" stroke-width="1.1"><circle cx="8" cy="8" r="6.5"/><ellipse cx="8" cy="8" rx="3" ry="6.5"/><path d="M1.5 8h13M2.6 4.8h10.8M2.6 11.2h10.8"/></svg>
    </li>
    <li>P.O Box 817 Wattlegrove
      <svg viewBox="0 0 16 16"><path d="M8 1.5 L15 8 H13 V14.5 H9.5 V10.5 H6.5 V14.5 H3 V8 H1 Z" fill="#fff"/></svg>
    </li>
    <li class="no-icon">WA, 6958</li>
  </ul>
</section>

<section class="card card-back">
  <div class="back-truck" role="img" aria-label="Large translucent illustration of a truck front"></div>
  <div class="web-address">www.<strong>brellhaul-example</strong>.com</div>
  <div class="legal">
    Brell Holdings Pty Ltd<br>
    (ACN 582 316 907)<br>
    ATF The Brell Discretionary Trust T/AS
  </div>
</section>

</body>
</html>
```